Sophisticated, clean website reflecting my feminine, playful side to sell my abstract art,

I need a website no more than 3 pages to showcase my paintings, a little about me and some contact info. I do abstracts so looking for something a little edgy, yet feminine and current.
Updates

Hi there, These are some artists websites that I Iike: Marnelvoss.com (I like how airy it is) peterwallombry.com garethpolvens.com (I like how it scrolls) I'll need a place for a photo ( a headshot-i do not have it yet so I'll need to be able to upload that later) as well as an area for my bio. Also, it's important that I will be able to upload any new photos and descriptions easily so it should be user friendly. Lastly, I like in a sunny place so would like to have this seem upbeat and playful as that is how i like to paint. thanks-I'm trying to upload my photos now -

Target Market(s)

ppl ages 35-70 who want large scale art for their homes

Industry/Entity Type

art

Coding

Coded - Design and coding required

Number of Pages Required

3 page

Colors

Designer to choose colors to be used in the design.

Requirements
Must have
• photos of my art, a place for my bio, be easy to reach me. tasteful-nothing too "in your face" -my clients are pretty high end and organized. They like clean lines
Nice to have
• sophisticated background, muted tones in the back-similar clean font throughout-no cursive
Should not have
• too many dark areas. Too many blocks of color. Too serious.

```html
<!DOCTYPE html>
<html lang="en">
<head>
<meta charset="utf-8">
<title>Lena Marwick — Abstract Art</title>
<link href="https://fonts.googleapis.com/css2?family=Questrial&family=Quicksand:wght@400;500;700&display=swap" rel="stylesheet">
<style>
  :root {
    --ink: #1c1c1c;
    --text: #3a3a3a;
    --muted: #6b6b6b;
    --gold: #b8ab86;
    --rule: #cfcfcf;
    --frame: #b9b9b9;
    --gallery-frame: #d2c9be;
    --arrow-dark: #2a2a2a;
    --arrow-soft: rgba(70,70,70,.55);
    --paper: #ffffff;
  }
  * { margin: 0; padding: 0; box-sizing: border-box; }
  html, body { width: 1200px; height: 2884px; overflow: hidden; background: var(--paper); }
  body { position: relative; font-family: "Quicksand", sans-serif; color: var(--text); }
  h1, h2 { font-weight: 400; }
  .abs { position: absolute; }

  /* Header */
  .brand { top: 28px; left: 0; width: 1200px; display: flex; justify-content: center; align-items: center; gap: 16px; }
  .brand-mark { width: 42px; height: 42px; background: var(--ink); }
  .brand-name { font-family: "Questrial", sans-serif; font-weight: 400; font-size: 42px; letter-spacing: 1px; color: var(--ink); line-height: 1; }
  .header-rule { top: 100px; left: 0; width: 1200px; height: 2px; background: #d6d6d6; }
  .nav-link { top: 121px; font-family: "Questrial", sans-serif; font-size: 16px; color: var(--ink); transform: translateX(-50%); letter-spacing: .3px; }
  .nav-link.active::after { content: ""; position: absolute; left: 0; right: 0; bottom: -10px; height: 2px; background: var(--ink); }
  .social { display: flex; align-items: center; gap: 6px; font-family: "Quicksand", sans-serif; font-size: 17px; color: var(--ink); }
  .social-dot { width: 30px; height: 30px; border-radius: 50%; background: var(--ink); }

  /* Hero */
  .hero { top: 165px; left: 0; width: 1200px; height: 644px;
    background:
      radial-gradient(ellipse 320px 260px at 15% 30%, #cfcac2 0%, transparent 70%),
      radial-gradient(ellipse 300px 300px at 45% 35%, #1f8e93 0%, transparent 70%),
      radial-gradient(ellipse 260px 240px at 25% 60%, #c06a22 0%, transparent 70%),
      radial-gradient(ellipse 280px 260px at 80% 40%, #e6e1d6 0%, transparent 70%),
      radial-gradient(ellipse 220px 200px at 92% 70%, #d9b54a 0%, transparent 70%),
      radial-gradient(ellipse 260px 220px at 65% 65%, #b5622a 0%, transparent 70%),
      linear-gradient(160deg, #3b4a48 0%, #1d5f66 40%, #2b2f33 100%); }
  .hero-welcome { top: 596px; left: 0; width: 1228px; text-align: center; font-family: "Questrial", sans-serif; color: #fff; font-size: 47px; letter-spacing: 1px; line-height: 1.1; }
  .hero-title { top: 652px; left: 0; width: 1244px; text-align: center; font-family: "Questrial", sans-serif; color: #fff; font-size: 72px; letter-spacing: 1px; line-height: 1.1; }
  .slider-arrow { width: 64px; height: 75px; display: flex; align-items: center; justify-content: center; }
  .slider-arrow.soft { background: var(--arrow-soft); }
  .slider-arrow.dark { background: var(--arrow-dark); }

  /* About */
  .about-frame { top: 920px; left: 53px; }
  .about-photo { top: 929px; left: 62px; width: 393px; height: 386px; background: linear-gradient(180deg, #f1f1f1 0%, #e6e4e1 60%, #f3f3f3 100%); }
  .section-title { font-family: "Questrial", sans-serif; font-weight: 400; font-size: 42px; color: var(--ink); letter-spacing: .5px; line-height: 1; }
  .gold-rule { height: 3px; background: var(--gold); }
  .about-title { top: 962px; left: 537px; }
  .about-rule { top: 1014px; left: 537px; width: 64px; }
  .about-copy { top: 1039px; left: 537px; width: 582px; font-size: 17px; line-height: 27px; text-align: justify; color: var(--text); }
  .about-copy p + p { margin-top: 14px; }

  /* Gallery */
  .gallery-title { top: 1475px; left: 0; width: 1178px; text-align: center; }
  .gallery-rule { top: 1527px; left: 559px; width: 64px; }
  .gallery-frame { top: 1565px; left: 124px; width: 972px; height: 616px; border: 6px solid var(--gallery-frame); }
  .gallery-painting { top: 1583px; left: 143px; width: 935px; height: 578px;
    background:
      radial-gradient(ellipse 220px 180px at 20% 30%, #5b6fa8 0%, transparent 70%),
      radial-gradient(ellipse 260px 220px at 45% 50%, #6b3f82 0%, transparent 70%),
      radial-gradient(ellipse 240px 200px at 75% 35%, #e7dccb 0%, transparent 70%),
      radial-gradient(ellipse 260px 220px at 80% 75%, #8b5a8e 0%, transparent 70%),
      radial-gradient(ellipse 200px 160px at 30% 80%, #a0684f 0%, transparent 70%),
      linear-gradient(135deg, #c9b9c6 0%, #7d5a8f 50%, #d8cabc 100%); }

  /* Contact */
  .contact-title { top: 2340px; left: 0; width: 1196px; text-align: center; }
  .contact-rule { top: 2389px; left: 553px; width: 90px; }
  .contact-lead { top: 2398px; left: 0; width: 1196px; text-align: center; font-size: 19px; color: var(--ink); }
  .contact-item { top: 2462px; width: 300px; transform: translateX(-50%); display: flex; flex-direction: column; align-items: center; gap: 14px; }
  .contact-icon { width: 56px; height: 56px; border-radius: 50%; background: var(--gold); display: flex; align-items: center; justify-content: center; }
  .contact-text { font-size: 21px; color: var(--ink); font-weight: 500; }

  /* Footer */
  .footer-brand { top: 2730px; left: 126px; display: flex; align-items: center; gap: 8px; }
  .footer-mark { width: 42px; height: 42px; background: var(--ink); }
  .footer-name { font-family: "Quicksand", sans-serif; font-weight: 700; font-size: 30px; color: var(--ink); }
  .footer-link { top: 2742px; font-family: "Questrial", sans-serif; font-size: 17px; color: var(--ink); transform: translateX(-50%); }
  .footer-rule { top: 2808px; left: 120px; width: 992px; height: 2px; background: var(--rule); }
  .copyright { top: 2828px; left: 0; width: 1212px; text-align: center; font-size: 14px; color: var(--muted); }
</style>
</head>
<body>

<header>
  <div class="abs brand">
    <span class="brand-mark"></span>
    <span class="brand-name">LENA MARWICK</span>
  </div>
  <div class="abs header-rule"></div>
  <nav>
    <span class="abs nav-link active" style="left:209px">HOME</span>
    <span class="abs nav-link" style="left:388px">ABOUT ME</span>
    <span class="abs nav-link" style="left:580px">GALLERY</span>
    <span class="abs nav-link" style="left:768px">CONTACT</span>
    <span class="abs social" style="top:116px;left:913px"><span class="social-dot"></span>@lmarwickart</span>
  </nav>
</header>

<section class="hero-section">
  <div class="abs hero" role="img" aria-label="Abstract painting in teal, orange, grey and white brushstrokes"></div>
  <div class="abs slider-arrow soft" style="top:424px;left:0">
    <svg width="22" height="32" viewBox="0 0 22 32"><polyline points="17,4 5,16 17,28" fill="none" stroke="#fff" stroke-width="4"/></svg>
  </div>
  <div class="abs slider-arrow soft" style="top:424px;left:1145px;width:55px">
    <svg width="22" height="32" viewBox="0 0 22 32"><polyline points="5,4 17,16 5,28" fill="none" stroke="#fff" stroke-width="4"/></svg>
  </div>
  <h2 class="abs hero-welcome">WELCOME TO</h2>
  <h1 class="abs hero-title">LENA MARWICK</h1>
</section>

<section class="about">
  <svg class="abs about-frame" width="420" height="420" viewBox="0 0 420 420">
    <polyline points="330,2 2,2 2,370" fill="none" stroke="var(--frame)" stroke-width="7"/>
    <polyline points="325,2 315,2 305,12" fill="none" stroke="var(--frame)" stroke-width="7"/>
    <polyline points="416,78 416,412 96,412" fill="none" stroke="var(--frame)" stroke-width="7"/>
    <line x1="96" y1="412" x2="86" y2="420" stroke="var(--frame)" stroke-width="7"/>
  </svg>
  <div class="abs about-photo" role="img" aria-label="Headshot of the artist"></div>
  <h2 class="abs section-title about-title">ABOUT ME</h2>
  <div class="abs gold-rule about-rule"></div>
  <div class="abs about-copy">
    <p>Lorem ipsum dolor sit amet, consectetur adipiscing elit, sed do eiusmod tempor incididunt ut labore et dolore magna aliqua. Ut enim ad minim veniam, quis nostrud exercitation</p>
    <p>Duis aute irure dolor in reprehenderit in voluptate velit esse cillum dolore eu fugiat nulla pariatur. Excepteur sint occaecat cupidatat non proident, sunt in culpa qui officia deserunt mollit anim id est laborum.Sed ut perspiciatis unde pariatur. Excepteur sint occaecat cupidatat non proident, sunt in culpa qui officia deserunt mollit anim id est laborum.Sed ut perspiciatis un</p>
  </div>
</section>

<section class="gallery">
  <h2 class="abs section-title gallery-title">PAINTING GALLERY</h2>
  <div class="abs gold-rule gallery-rule"></div>
  <div class="abs gallery-frame"></div>
  <div class="abs gallery-painting" role="img" aria-label="Abstract painting with purple, blue and rust floral bursts on a cream ground"></div>
  <div class="abs slider-arrow dark" style="top:1819px;left:0">
    <svg width="22" height="32" viewBox="0 0 22 32"><polyline points="17,4 5,16 17,28" fill="none" stroke="#fff" stroke-width="4"/></svg>
  </div>
  <div class="abs slider-arrow dark" style="top:1819px;left:1145px;width:55px">
    <svg width="22" height="32" viewBox="0 0 22 32"><polyline points="5,4 17,16 5,28" fill="none" stroke="#fff" stroke-width="4"/></svg>
  </div>
</section>

<section class="contact">
  <h2 class="abs section-title contact-title">CONTACT ME</h2>
  <div class="abs gold-rule contact-rule"></div>
  <p class="abs contact-lead">Lorem ipsum dolor sit amet consectetur adipiscing elit</p>

  <div class="abs contact-item" style="left:313px">
    <span class="contact-icon">
      <svg width="30" height="30" viewBox="0 0 24 24"><path d="M6.6 10.8a15.1 15.1 0 0 0 6.6 6.6l2.2-2.2c.3-.3.7-.4 1-.2 1.1.4 2.3.6 3.6.6.6 0 1 .4 1 1V20c0 .6-.4 1-1 1A17 17 0 0 1 3 4c0-.6.4-1 1-1h3.5c.6 0 1 .4 1 1 0 1.3.2 2.5.6 3.6.1.3 0 .7-.2 1z" fill="#fff"/></svg>
    </span>
    <span class="contact-text">(555) 284 3619</span>
  </div>
  <div class="abs contact-item" style="left:612px">
    <span class="contact-icon">
      <svg width="32" height="24" viewBox="0 0 32 24"><rect x="2" y="2" width="28" height="20" fill="none" stroke="#fff" stroke-width="2.5"/><polyline points="2,2 16,14 30,2" fill="none" stroke="#fff" stroke-width="2.5"/><line x1="2" y1="22" x2="12" y2="11" stroke="#fff" stroke-width="2"/><line x1="30" y1="22" x2="20" y2="11" stroke="#fff" stroke-width="2"/></svg>
    </span>
    <span class="contact-text">lenamarwick@info.com</span>
  </div>
  <div class="abs contact-item" style="left:917px">
    <span class="contact-icon"></span>
    <span class="contact-text">@lmarwickart</span>
  </div>
</section>

<footer>
  <div class="abs footer-brand">
    <span class="footer-mark"></span>
    <span class="footer-name">LENA MARWICK</span>
  </div>
  <span class="abs footer-link" style="left:541px">ABOUT ME</span>
  <span class="abs footer-link" style="left:687px">GALLERY</span>
  <span class="abs footer-link" style="left:829px">CONTACT</span>
  <span class="abs social" style="top:2735px;left:943px"><span class="social-dot"></span>@lmarwickart</span>
  <div class="abs footer-rule"></div>
  <p class="abs copyright">© 2022 Lena Marwick &nbsp; All Rights Reserved</p>
</footer>

</body>
</html>
```